Maplecrest Disability - Social Security Disability Attorneys

Our company is expanding to attract clients nationwide for our social security disability practice. We have a logo, but I am looking for a creative and elegant letterhead that projects an image of being technologically advanced but still professional enough for the legal field. I am looking for the "wow factor" combined with this is still professional enough for a law practice.

Requesting letterhead and business card design
Updates

Had to update and change the logo. The previous logo had a typo. Please send updates with the new logo for consideration. The letterhead and business cards should be professional enough to be used for a law firm. Thanks.

Industry/Entity Type

Law Practice, Law Firm, Healthcare Industry, Government

Colors

Designer to choose colors to be used in the design.

Requirements
Nice to have
• **Please create a vertical design for the business card**

```html
<!DOCTYPE html>
<html lang="en">
<head>
<meta charset="utf-8">
<title>Maplecrest Disability – Stationery</title>
<link href="https://fonts.googleapis.com/css2?family=Lato:wght@400;700&family=Figtree:wght@400;500;700&family=Allura&display=swap" rel="stylesheet">
<style>
  :root{
    --backdrop:#c4c4c6;
    --paper:#ffffff;
    --ink:#1e1e1e;
    --brand-blue:#4169d6;
    --card-blue:#5672bc;
    --brand-orange:#f07f22;
  }
  *{margin:0;padding:0;box-sizing:border-box}
  html,body{width:1200px;height:848px;overflow:hidden;background:var(--backdrop)}
  .canvas{position:relative;width:1200px;height:848px}

  /* Letterhead */
  .letterhead{position:absolute;left:151px;top:118px;width:455px;height:623px;background:var(--paper);overflow:hidden;font-family:"Lato",sans-serif;color:var(--ink)}
  .brand{position:absolute;display:flex;align-items:center;gap:5px;color:var(--brand-blue);font-weight:400;letter-spacing:.06em;text-transform:uppercase;white-space:nowrap}
  .letterhead .brand{left:25px;top:58px;font-size:12px}
  .brand-dot{width:7px;height:7px;border-radius:50%;background:var(--brand-orange);flex:none}
  .contact{position:absolute;left:321px;top:36px;border-left:1px solid var(--brand-orange);padding-left:6px;font-family:"Figtree",sans-serif;font-size:7.3px;line-height:10.4px}
  .contact p{white-space:nowrap}
  .contact .row{display:flex;align-items:center;gap:5px;margin-top:1.6px}
  .contact .row:first-of-type{margin-top:2.4px}
  .icon{width:7px;height:7px;flex:none}
  .letter-body{position:absolute;left:25px;top:147px;width:405px;font-size:9.1px;line-height:10.2px}
  .letter-date{margin-bottom:10.5px}
  .recipient{margin-bottom:10.5px}
  .salutation{font-weight:700;font-size:11px;margin:6px 0 9px}
  .para{text-align:justify;margin-bottom:9.5px;line-height:9.8px}
  .closing{margin-top:20px}
  .signature{font-family:"Allura",cursive;font-size:24px;line-height:28px;margin-top:9px;margin-left:2px}
  .letter-wave{position:absolute;left:0;bottom:0;width:455px;height:100px}

  /* Business cards */
  .card{position:absolute;top:234px;width:213px;height:373px;overflow:hidden;font-family:"Figtree",sans-serif}
  .card-front{left:627px;background:var(--paper);color:var(--ink);text-align:center}
  .card-back{left:864px;background:var(--card-blue);color:#fff;text-align:center}
  .card .brand{left:0;right:0;justify-content:center;font-family:"Figtree",sans-serif;font-size:12px}
  .card-front .brand{top:75px}
  .card-back .brand{top:84px;color:#fff}
  .holder-name{position:absolute;left:0;right:0;top:132px;font-weight:700;font-size:12.5px;color:var(--brand-orange)}
  .holder-role{position:absolute;left:0;right:0;top:148px;display:flex;align-items:center;justify-content:center;gap:3px;font-size:10px}
  .holder-role::before,.holder-role::after{content:"";width:28px;height:1px;background:var(--brand-orange)}
  .card-address{position:absolute;left:0;right:0;top:191px;font-size:9.2px;line-height:12.3px}
  .card-icons{position:absolute;left:0;right:0;top:233px;display:flex;justify-content:center;gap:17px}
  .card-icons .icon{width:9px;height:9px}
  .card-lines{position:absolute;left:0;right:0;top:259px;font-size:9.2px;line-height:14px}
  .card-wave{position:absolute;left:0;bottom:0;width:213px;height:60px}
  .sectors{position:absolute;left:0;right:0;top:316px;font-size:8.8px;line-height:12.5px}
</style>
</head>
<body>
<main class="canvas">

  <!-- Letterhead -->
  <section class="letterhead" aria-label="Letterhead">
    <div class="brand"><span class="brand-dot"></span>Maplecrest Disability</div>

    <address class="contact" style="font-style:normal">
      <p>Suite 4, level 12, Alder Lane</p>
      <p>Denver CO 80202</p>
      <div class="row">
        <svg class="icon" viewBox="0 0 10 10"><path d="M2 1 L4 3 L3 4.2 Q4.2 6 5.8 7 L7 6 L9 8 L7.6 9.3 Q3.5 8.5 0.8 2.4Z" fill="var(--brand-orange)"/></svg>
        <p>555-014-2290</p>
      </div>
      <div class="row">
        <svg class="icon" viewBox="0 0 10 10"><rect x="0.5" y="2" width="9" height="6" fill="var(--brand-orange)"/><path d="M0.5 2 L5 5.5 L9.5 2" fill="none" stroke="#fff" stroke-width=".8"/></svg>
        <p>info@maplecrestdisability.com</p>
      </div>
      <div class="row">
        <svg class="icon" viewBox="0 0 10 10"><circle cx="5" cy="5" r="4.5" fill="var(--brand-orange)"/><path d="M0.5 5 H9.5 M5 0.5 Q2.5 5 5 9.5 M5 0.5 Q7.5 5 5 9.5" fill="none" stroke="#fff" stroke-width=".6"/></svg>
        <p>www.maplecrestdisability.com</p>
      </div>
    </address>

    <div class="letter-body">
      <p class="letter-date">January-03-2020</p>
      <p class="recipient">Mr, Alan Reyes<br>President</p>
      <p class="recipient">Brookline Corporation<br>123 Street Name, Suite# 10<br>City, State, 120023</p>
      <p class="salutation">Dear Mr, Alan</p>
      <p class="para">Lorem ipsum dolor sit amet, consectetur adipisicing elit, sed do eiusmod tempor incididunt ut labore et dolore magna aliqua. Ut enim ad minim veniam, quis nostrud exercitation ullamco laboris nisi ut aliquip ex ea commodo consequat. Duis aute irure dolor in reprehenderit in voluptate velit esse cillum dolore eu fugiat nulla pariatur.</p>
      <p class="para">Lorem ipsum dolor sit amet, consectetur adipisicing elit, sed do eiusmod tempor incididunt ut labore et dolore magna aliqua. Ut enim ad minim veniam, quis nostrud exercitation ullamco laboris nisi ut aliquip ex ea commodo consequat. Duis aute irure dolor in reprehenderit in voluptate velit esse cillum dolore eu fugiat nulla pariatur.</p>
      <p class="para">Lorem ipsum dolor sit amet, consectetur adipisicing elit, sed do eiusmod tempor incididunt ut labore et dolore magna aliqua. Ut enim ad minim veniam, quis nostrud exercitation ullamco laboris nisi ut aliquip ex ea commodo consequat.</p>
      <p class="para">Excepteur sint occaecat cupidatat non proident, sunt in culpa qui officia deserunt mollit anim id est laborum. re et dolore magnam aliquam quaerat voluptatem.</p>
      <p class="closing">Regards</p>
      <p class="signature">Daniel Hart</p>
    </div>

    <svg class="letter-wave" viewBox="0 0 455 100" preserveAspectRatio="none" aria-hidden="true">
      <path d="M152 57 Q330 46 455 1 L455 12 Q330 52 152 57Z" fill="var(--brand-orange)"/>
      <path d="M0 56 Q120 63 250 53 Q380 41 455 17 L455 100 L0 100Z" fill="var(--brand-blue)"/>
    </svg>
  </section>

  <!-- Business card front -->
  <section class="card card-front" aria-label="Business card front">
    <div class="brand"><span class="brand-dot"></span>Maplecrest Disability</div>
    <p class="holder-name">ELLIS CARROW</p>
    <p class="holder-role">Co-Founder</p>
    <p class="card-address">Suite 4, level 12, Alder Lane<br>Denver CO 80202</p>
    <div class="card-icons">
      <svg class="icon" viewBox="0 0 10 10"><path d="M2 1 L4 3 L3 4.2 Q4.2 6 5.8 7 L7 6 L9 8 L7.6 9.3 Q3.5 8.5 0.8 2.4Z" fill="var(--brand-orange)"/></svg>
      <svg class="icon" viewBox="0 0 10 10"><rect x="0.5" y="2" width="9" height="6" fill="var(--brand-orange)"/><path d="M0.5 2 L5 5.5 L9.5 2" fill="none" stroke="#fff" stroke-width=".8"/></svg>
      <svg class="icon" viewBox="0 0 10 10"><circle cx="5" cy="5" r="4.5" fill="var(--brand-orange)"/><path d="M0.5 5 H9.5 M5 0.5 Q2.5 5 5 9.5 M5 0.5 Q7.5 5 5 9.5" fill="none" stroke="#fff" stroke-width=".6"/></svg>
    </div>
    <p class="card-lines">555-014-2290<br>info@maplecrestdisability.com<br>www.maplecrestdisability.com</p>
    <svg class="card-wave" viewBox="0 0 213 60" preserveAspectRatio="none" aria-hidden="true">
      <path d="M73 29 Q160 22 213 2 L213 8 Q160 27 73 29Z" fill="var(--brand-orange)"/>
      <path d="M0 27 Q70 33 130 26 Q180 20 213 10 L213 60 L0 60Z" fill="var(--card-blue)"/>
    </svg>
  </section>

  <!-- Business card back -->
  <section class="card card-back" aria-label="Business card back">
    <div class="brand">Maplecrest Disability</div>
    <p class="sectors">Law Practice, Law Firm,<br>Healthcare Industry, Government</p>
  </section>

</main>
</body>
</html>
```